single page with calendar booking ability

a single web page that has the ability to book calendar times and dates, also needs to be able to link to my other business social media seamlessly. I don't want to get multiple developers and or agency's involved, I want you the web designer to design it and make sure it's up and works as described
. The boats we work on are between 20 feet to 40 feet, bow riders , cabin cruisers, and center consoles. The brands that we work on include but are not limited to Velmora, Praxen, Dunby Vale, Lark mil, Quilvane, Brevik, Drelo, and many more. Winterization and shrink wrapping is completely different than graphic wrapping, we do not do graphic's wrapping. Also, only 5% of our business will be auto detailing, the rest will be boats on trailers. Please ensure that the calendar booking system is intergraded and not a surprise to me later

Target Market(s)

Lakes region New Hampshire

Industry/Entity Type

marine

Coding

Coded - Design and coding required

Number of Pages Required

1 page

Colors
0054AA
0677BA
7BADD7
CADEEF
E8F1F8
00AB8E
00BBA5
67D7C9
C6EFE9
E9F9F6
EE7325
F08F49
F5BC92
FAE3D3
FDF4ED

Requirements
Must have
• calendar booking capability
Nice to have
• Pictures of boats being shrink wrapped for the winter season, Nice before and after pictures of boats detailed, only 5% of our business is auto detailing
Should not have
• Large yachts, lots of sail boats as we only do a few, graphics wrapping.. we don't graphic wrap

```html
<!DOCTYPE html>
<html lang="en">
<head>
<meta charset="utf-8">
<title>Keelwright Marine and Auto — Book a Service</title>
<link rel="stylesheet" href="https://fonts.googleapis.com/css2?family=Rubik:wght@400;500;700&display=swap">
<style>
  :root {
    --navy-deep: #0c1f33;
    --navy: #11263d;
    --ocean-dark: #153a57;
    --sky: #4cc3f0;
    --sky-light: #8fd9f7;
    --sea: #1a94cf;
    --sea-deep: #1478b3;
    --orange: #e8401f;
    --white: #ffffff;
    --muted: #8c97a3;
    --outline: #1e9be0;
    --hull-light: #e4e7ea;
    --hull-mid: #8a9bb3;
    --hull-dark: #4a5f80;
  }
  * { box-sizing: border-box; margin: 0; padding: 0; }
  html, body {
    width: 1200px; height: 800px; overflow: hidden;
    background: var(--navy);
    font-family: "Rubik", Arial, sans-serif;
    color: var(--white);
  }
  .page {
    position: relative; width: 1200px; height: 800px; overflow: hidden;
    background: radial-gradient(ellipse 70% 60% at 30% 15%, var(--ocean-dark) 0%, var(--navy) 60%, var(--navy-deep) 100%);
  }
  .ocean-photo {
    position: absolute; left: 0; top: 0; width: 760px; height: 420px;
    background: radial-gradient(ellipse 60% 70% at 40% 20%, rgba(34,84,116,.55) 0%, rgba(17,38,61,0) 75%);
  }
  .brand {
    position: absolute; left: 88px; top: 52px;
    display: flex; align-items: center; gap: 8px;
    font-weight: 700; font-size: 19px; color: var(--sky);
  }
  .brand-dot { width: 14px; height: 14px; border-radius: 50%; background: var(--orange); }
  .nav {
    position: absolute; right: 90px; top: 29px;
    display: flex; align-items: center; gap: 18px;
    font-size: 15px; font-weight: 500;
  }
  .nav a { color: var(--white); text-decoration: none; }
  .nav .login {
    border: 2px solid var(--outline); border-radius: 16px;
    width: 96px; height: 31px; display: flex; align-items: center; justify-content: center;
  }
  .nav .lang { display: flex; align-items: center; gap: 4px; }
  .headline {
    position: absolute; left: 86px; top: 288px;
    font-weight: 700; font-size: 67px; line-height: 67px; letter-spacing: .5px;
  }
  .headline .accent { color: var(--orange); display: block; }
  .hero-circle {
    position: absolute; left: 625px; top: 139px; width: 483px; height: 483px; border-radius: 50%;
    background: linear-gradient(180deg, var(--sky) 0%, var(--sky-light) 40%, var(--sea) 62%, var(--sea-deep) 100%);
  }
  .hero-boat {
    position: absolute; left: 496px; top: 316px; width: 682px; height: 164px;
    border-radius: 14px;
    background: linear-gradient(180deg, var(--hull-light) 0%, var(--hull-mid) 55%, var(--hull-dark) 100%);
  }
  .booking { position: absolute; left: 89px; top: 641px; width: 1022px; height: 50px; }
  .field { position: absolute; top: 0; }
  .field-label { font-size: 18px; color: var(--muted); font-weight: 500; line-height: 1; }
  .field-value {
    margin-top: 7px; display: flex; align-items: center; gap: 16px;
    font-size: 24px; font-weight: 500; line-height: 1;
  }
  .field-value svg { width: 22px; height: 22px; }
  .field--calendar { left: 0; }
  .field--time { left: 244px; }
  .field--date { left: 453px; }
  .book-now {
    position: absolute; left: 803px; top: 2px; width: 215px; height: 46px;
    background: var(--orange); border: 0; border-radius: 23px;
    color: var(--white); font: 700 19px "Rubik", Arial, sans-serif; letter-spacing: .3px;
  }
  .footer {
    position: absolute; left: 0; right: 0; top: 755px;
    text-align: center; font-size: 17px; font-weight: 500;
  }
</style>
</head>
<body>
<main class="page">
  <div class="ocean-photo" role="img" aria-label="Aerial photo of dark open water with a sailboat"></div>

  <div class="brand"><span class="brand-dot"></span>Keelwright Marine and Auto</div>

  <nav class="nav">
    <a href="#">Register</a>
    <a href="#" class="login">Login</a>
    <a href="#" class="lang">En
      <svg width="10" height="10" viewBox="0 0 10 10"><path d="M1 3l4 4 4-4" fill="none" stroke="#fff" stroke-width="1.6"/></svg>
    </a>
  </nav>

  <h1 class="headline"><span class="accent">Keelwright</span>Marine And<br>Auto</h1>

  <div class="hero-circle" role="img" aria-label="Photo of bright sky over blue sea"></div>
  <div class="hero-boat" role="img" aria-label="Photo of a blue and white bowrider boat, side view"></div>

  <section class="booking">
    <div class="field field--calendar">
      <div class="field-label">Calendar</div>
      <div class="field-value">Fri, 22 Mar
        <svg viewBox="0 0 22 22" fill="none" stroke="#fff" stroke-width="1.6"><rect x="2" y="4" width="18" height="16" rx="3"/><path d="M7 2v4M15 2v4M2 9h18"/><circle cx="7" cy="13" r=".6" fill="#fff"/><circle cx="11" cy="13" r=".6" fill="#fff"/><circle cx="15" cy="13" r=".6" fill="#fff"/><circle cx="7" cy="16.5" r=".6" fill="#fff"/><circle cx="11" cy="16.5" r=".6" fill="#fff"/><circle cx="15" cy="16.5" r=".6" fill="#fff"/></svg>
      </div>
    </div>
    <div class="field field--time">
      <div class="field-label">Times</div>
      <div class="field-value">7, 00 Am
        <svg viewBox="0 0 22 22" fill="none" stroke="#fff" stroke-width="1.6"><rect x="2" y="2" width="18" height="18" rx="5"/><path d="M11 6v5.5l3 2.5"/></svg>
      </div>
    </div>
    <div class="field field--date">
      <div class="field-label">Date</div>
      <div class="field-value">July 3, Today
        <svg viewBox="0 0 22 22" fill="none" stroke="#fff" stroke-width="1.6"><rect x="2" y="4" width="18" height="16" rx="3"/><path d="M7 2v4M15 2v4M2 9h18"/><circle cx="7" cy="13" r=".6" fill="#fff"/><circle cx="11" cy="13" r=".6" fill="#fff"/><circle cx="15" cy="13" r=".6" fill="#fff"/><circle cx="7" cy="16.5" r=".6" fill="#fff"/><circle cx="11" cy="16.5" r=".6" fill="#fff"/><circle cx="15" cy="16.5" r=".6" fill="#fff"/></svg>
      </div>
    </div>
    <button class="book-now" type="button">BOOK NOW</button>
  </section>

  <footer class="footer">©Copyright 2021 | All Rights Reseved</footer>
</main>
</body>
</html>
```